Pellowar

We need logo and wesbsite for a software development company based out of Hyderabad, India focused on startups and mid sized companies focused on build a new software products in USA and Europe countires.

Target Market(s)

startup and midsized companies in teh USA and Europe for software product development.

Industry/Entity Type

software development

Coding

Coded - Design and coding required

Number of Pages Required

5+ page

Requirements
Must have
• latest design concepts and very elegant
Nice to have
• each page should have images that reflects the content
Should not have
• too many colors

```html
<!DOCTYPE html>
<html lang="en">
<head>
<meta charset="utf-8">
<title>Pellowar — Software Product Development</title>
<link href="https://fonts.googleapis.com/css2?family=Montserrat:wght@500;600;700;800&family=Poppins:wght@300;400;500;600&display=swap" rel="stylesheet">
<style>
:root{
  --blue:#1552d6;
  --blue-dark:#0d3fb0;
  --navy:#0b1b3d;
  --ink:#1c1c24;
  --text:#55586a;
  --muted:#8a8d99;
  --grey-band:#ededed;
  --white:#ffffff;
  --line:#e3e5ec;
}
*{margin:0;padding:0;box-sizing:border-box}
html,body{width:1200px;height:4016px;overflow:hidden}
body{font-family:'Poppins',sans-serif;color:var(--text);background:var(--white);position:relative}
section,header,nav,footer{overflow:hidden}
h1,h2,h3,h4,.logo{font-family:'Montserrat',sans-serif}
a{color:inherit;text-decoration:none}

/* top bar */
.topbar{height:48px;background:#f1f1f3;display:flex;align-items:center;justify-content:space-between;padding:0 112px;font-size:15px;color:var(--ink)}
.topbar .contact{display:flex;gap:34px;align-items:center}
.topbar .contact span{display:flex;align-items:center;gap:8px}
.social{display:flex;gap:10px}
.social i{width:26px;height:26px;border-radius:50%;border:1.5px solid var(--ink);display:block}

/* nav */
.nav{height:80px;display:flex;align-items:center;justify-content:space-between;padding:0 112px;border-bottom:1px solid var(--line)}
.logo{font-size:38px;font-weight:800;color:var(--blue)}
.menu{display:flex;align-items:center;gap:40px;font-size:16px;color:var(--ink)}
.menu .active{color:var(--blue);border-bottom:2px solid var(--blue);padding-bottom:6px}
.btn-login{background:var(--blue);color:#fff;padding:12px 58px;border-radius:12px 0 12px 0;font-weight:500;margin-left:40px}

/* hero */
.hero{position:relative;height:600px;background:linear-gradient(100deg,#3a3430 0%,#5a4a42 30%,#2a3344 60%,#10182c 100%)}
.hero .shade{position:absolute;inset:0;background:linear-gradient(90deg,rgba(10,16,30,0) 40%,rgba(10,16,30,.7) 75%)}
.hero-text{position:absolute;left:662px;top:136px;width:440px;color:#fff}
.hero-text h1{font-size:54px;font-weight:600;letter-spacing:2px;line-height:1.15}
.hero-text p{font-size:15px;line-height:1.6;margin:22px 0 36px;color:#d9dce6}
.btn{display:inline-block;background:var(--blue);color:#fff;font-size:15px;padding:13px 40px;border-radius:14px 0 14px 0}
.dots{position:absolute;bottom:18px;left:50%;transform:translateX(-50%);display:flex;gap:10px}
.dots i{width:10px;height:10px;border-radius:50%;background:rgba(255,255,255,.5);display:block}
.dots i.on{background:#fff}

/* about */
.about{position:relative;height:572px}
.about .ring{position:absolute;left:128px;top:78px;width:424px;height:424px;border-radius:50%;border:14px solid var(--blue)}
.about .portrait{position:absolute;left:116px;top:66px;width:420px;height:420px;border-radius:50%;background:radial-gradient(circle at 50% 40%,#c9b8a8,#7c8a98 70%,#4f5b6a)}
.about-text{position:absolute;left:606px;top:76px;width:490px}
.about-text h4{font-size:18px;font-weight:600;color:var(--ink);letter-spacing:.5px}
.about-text h2{font-size:34px;font-weight:700;color:var(--ink);margin:4px 0 20px}
.about-text p{font-size:15px;line-height:1.65;margin-bottom:20px}

/* product */
.product{height:580px;background:var(--grey-band);text-align:center;padding-top:56px}
.section-title{font-size:34px;font-weight:700;color:var(--ink);line-height:1.2}
.section-sub{font-size:17px;color:var(--ink);margin:14px auto 0;width:720px;line-height:1.5}
.roles{display:flex;gap:20px;justify-content:center;margin-top:44px;align-items:flex-end}
.role{width:240px;height:340px;border-radius:34px 0 34px 0;position:relative;overflow:hidden;text-align:left}
.role .photo{position:absolute;inset:0}
.role .label{position:absolute;left:0;right:0;bottom:0;height:110px;background:linear-gradient(0deg,rgba(21,82,214,.95),rgba(21,82,214,0));color:#fff;font-family:'Montserrat',sans-serif;font-weight:700;font-size:19px;padding:56px 22px 0}
.role.feature{background:var(--blue);color:#fff;text-align:center;padding:44px 26px 0}
.role.feature h3{font-size:22px;font-weight:700}
.role.feature p{font-size:14px;line-height:1.6;margin:16px 0 0;color:#dbe4ff}
.role.feature .more{display:inline-block;margin-top:22px;font-size:15px;border-bottom:2px solid #fff;padding-bottom:3px}

/* team */
.team{height:700px;text-align:center;padding-top:78px}
.team .section-sub{font-size:15px;width:780px;color:var(--text)}
.steps{display:flex;gap:36px;justify-content:center;margin-top:50px}
.step{width:300px;height:330px;background:#fff;box-shadow:0 4px 24px rgba(20,30,60,.12);border-radius:6px;padding:30px 26px;text-align:left}
.step .icon{width:68px;height:68px;border-radius:50%;background:var(--blue);margin:0 auto 22px;display:flex;align-items:center;justify-content:center}
.step h3{font-size:16px;font-weight:700;color:var(--blue);text-align:center;margin-bottom:18px;white-space:nowrap}
.step p{font-size:14px;line-height:1.65}

/* case study */
.case{height:340px;background:linear-gradient(90deg,#0a1a3c,#13306a 55%,#0b1b3d);text-align:center;color:#fff;padding-top:52px}
.case h2{font-size:34px;font-weight:700;letter-spacing:1px}
.case p{font-size:16px;line-height:1.6;width:860px;margin:18px auto 26px;color:#e3e8f5}
.btn-white{display:inline-block;background:#fff;color:var(--blue);padding:13px 40px;border-radius:14px 0 14px 0;font-size:15px}

/* blog */
.blog{height:660px;text-align:center;padding-top:62px}
.blog .section-title{color:var(--blue)}
.posts{display:flex;gap:36px;justify-content:center;margin-top:48px}
.post{width:300px;height:400px;background:#fff;box-shadow:0 4px 22px rgba(20,30,60,.13);text-align:left}
.post .photo{height:200px}
.post .body{padding:18px 24px}
.post .date{font-size:14px;color:var(--ink)}
.post h3{font-family:'Poppins',sans-serif;font-size:18px;font-weight:500;color:var(--ink);line-height:1.35;margin:10px 0 8px}
.post p{font-size:13px;color:var(--muted);line-height:1.5}
.post .btn{padding:9px 28px;font-size:13px;margin-top:16px}

/* footer */
.footer{height:436px;background:var(--blue);color:#fff;padding:54px 112px 0;position:relative}
.cols{display:flex}
.cols .brand{width:300px}
.cols .brand .logo{color:#fff;font-size:34px}
.cols .brand p{font-size:14px;line-height:1.55;margin-top:18px;color:#e2e9ff;padding-right:20px}
.col{width:190px}
.col h4{font-size:24px;font-weight:600;margin-bottom:22px}
.col li{list-style:none;font-size:14px;line-height:1.9}
.col.address{width:300px}
.col.address li{display:flex;gap:12px;align-items:flex-start;margin-bottom:14px;line-height:1.5}
.copy{position:absolute;left:112px;right:112px;bottom:50px;border-top:1px solid rgba(255,255,255,.45);padding-top:28px;text-align:center;font-size:15px}
</style>
</head>
<body>

<header class="topbar">
  <div class="contact">
    <span><svg width="18" height="14" viewBox="0 0 18 14"><rect x="1" y="1" width="16" height="12" rx="1.5" fill="none" stroke="#1c1c24" stroke-width="1.5"/><path d="M1 2l8 6 8-6" fill="none" stroke="#1c1c24" stroke-width="1.5"/></svg>info@pellowar.com</span>
    <span><svg width="16" height="16" viewBox="0 0 16 16"><path d="M3 1h3l1.5 4-2 1.5a9 9 0 0 0 4 4l1.5-2 4 1.5v3a1 1 0 0 1-1 1C7 14 2 9 2 2a1 1 0 0 1 1-1z" fill="#1c1c24"/></svg>+1 555 010 2040</span>
  </div>
  <div class="social"><i></i><i></i><i></i></div>
</header>

<nav class="nav">
  <div class="logo">Pellowar</div>
  <div class="menu">
    <a class="active">Home</a><a>About Us</a><a>software</a><a>Contact us</a>
    <a class="btn-login">Login</a>
  </div>
</nav>

<section class="hero">
  <div role="img" aria-label="Photo of a team of developers working together at laptops" style="position:absolute;inset:0"></div>
  <div class="shade"></div>
  <div class="hero-text">
    <h1>WELCOME TO<br>PELLOWAR</h1>
    <p>We build elegant software products for startups and growing companies, from first idea to scalable release across USA and Europe.</p>
    <a class="btn">Get started</a>
  </div>
  <div class="dots"><i class="on"></i><i></i><i></i></div>
</section>

<section class="about">
  <div class="ring"></div>
  <div class="portrait" role="img" aria-label="Portrait photo of a smiling team member with glasses"></div>
  <div class="about-text">
    <h4>WHO WE ARE</h4>
    <h2>ABOUT US</h2>
    <p>Teams are the essence of every business. They can create wonders if built with perfection.</p>
    <p>We are a group of entrepreneurs, technocrats, software architects, and delivery heads who have come together to serve startups, product companies, and enterprises with their product development. We are prompt in understanding your product and help design, build, maintain and operate your product. Pellowar quickly set up a team of VR experts, Business Analysts, Developers and QA resources to build the best team to deliver the product.</p>
    <a class="btn">Learn More</a>
  </div>
</section>

<section class="product">
  <h2 class="section-title">BUILD YOUR PRODUCT</h2>
  <p class="section-sub">The competition to get the best resources, robust design, and scalable technology is overwhelming</p>
  <div class="roles">
    <div class="role"><div class="photo" role="img" aria-label="Photo of a project manager in an office" style="background:linear-gradient(160deg,#9fb4cc,#4c6386)"></div><div class="label">Project Manager</div></div>
    <div class="role feature">
      <h3>Team Lead</h3>
      <p>Startup owners must see the CTO mindset while building a software product.</p>
      <p>Focus on the outcome and we value the tiny technical</p>
      <a class="more">READ MORE</a>
    </div>
    <div class="role"><div class="photo" role="img" aria-label="Photo of a business analyst reviewing charts" style="background:linear-gradient(160deg,#b9c5d6,#5a6f92)"></div><div class="label">Business analyst</div></div>
    <div class="role"><div class="photo" role="img" aria-label="Photo of developers working at a desk" style="background:linear-gradient(160deg,#c9ccd4,#61708e)"></div><div class="label">Developers</div></div>
  </div>
</section>

<section class="team">
  <h2 class="section-title">BUILD YOUR TEAM</h2>
  <p class="section-sub">Break free from traditional recruiting with us. At Pellowar, we help you achieve the right organizational matrix with rockstars who can take your business to the next level</p>
  <div class="steps">
    <div class="step">
      <div class="icon"><svg width="34" height="34" viewBox="0 0 34 34"><path d="M7 18l7 7 13-15" fill="none" stroke="#fff" stroke-width="3.5" stroke-linecap="round" stroke-linejoin="round"/></svg></div>
      <h3>Pass cognitive aptitude test</h3>
      <p>Accepting job applications from the world means every role at Pellowar receives thousands of applications. We find that the most reliable way to</p>
    </div>
    <div class="step">
      <div class="icon"><svg width="34" height="34" viewBox="0 0 34 34"><path d="M7 18l7 7 13-15" fill="none" stroke="#fff" stroke-width="3.5" stroke-linecap="round" stroke-linejoin="round"/></svg></div>
      <h3>Pass English proficiency test.</h3>
      <p>Someday, technological advancements will make it possible for teams to collaborate without sharing a common</p>
    </div>
    <div class="step">
      <div class="icon"><svg width="34" height="34" viewBox="0 0 34 34"><path d="M7 18l7 7 13-15" fill="none" stroke="#fff" stroke-width="3.5" stroke-linecap="round" stroke-linejoin="round"/></svg></div>
      <h3>Prove real-world job skills.</h3>
      <p>Of course, there's much more to being a great worker than intelligence and language skills. The next step is to</p>
    </div>
  </div>
</section>

<section class="case" aria-label="Case study">
  <h2>CASE STUDY</h2>
  <p>Many business owners have great ideas but no experience with the actual product. Once you have an idea in mind, you will require software development for at some point – whether your concept is for next-generation software or an inventive approach to offering an existing service. It might also be the development of a mobile app or web-based software.</p>
  <a class="btn-white">Read more</a>
</section>

<section class="blog">
  <h2 class="section-title">OUR LASTEST BLOG</h2>
  <div class="posts">
    <article class="post">
      <div class="photo" role="img" aria-label="Photo of two developers discussing code" style="background:linear-gradient(135deg,#8d8a90,#2e3444)"></div>
      <div class="body"><div class="date">January 25, 2022</div><h3>Sed ut perspiciatis unde omnis iste natus error sit</h3><p>Lorem ipsum dolor sit amet consectetur adipiscing elit</p><a class="btn">Read more</a></div>
    </article>
    <article class="post">
      <div class="photo" role="img" aria-label="Photo of a developer at multiple monitors" style="background:linear-gradient(135deg,#6f7a8c,#1d2536)"></div>
      <div class="body"><div class="date">January 25, 2022</div><h3>Sed ut perspiciatis unde omnis iste natus error sit</h3><p>Lorem ipsum dolor sit amet consectetur adipiscing elit</p><a class="btn">Read more</a></div>
    </article>
    <article class="post">
      <div class="photo" role="img" aria-label="Photo of programmers working in an office" style="background:linear-gradient(135deg,#9aa3b2,#343c4e)"></div>
      <div class="body"><div class="date">January 25, 2022</div><h3>Sed ut perspiciatis unde omnis iste natus error sit</h3><p>Lorem ipsum dolor sit amet consectetur adipiscing elit</p><a class="btn">Read more</a></div>
    </article>
  </div>
</section>

<footer class="footer">
  <div class="cols">
    <div class="brand">
      <div class="logo">Pellowar</div>
      <p>Sed ut perspiciatis unde omnis iste natus error sit voluptatem accusantium doloremque</p>
    </div>
    <div class="col"><h4>Quicklink</h4><ul><li>Home</li><li>About us</li><li>software</li><li>Contact us</li></ul></div>
    <div class="col"><h4>Support</h4><ul><li>Termsconditions</li><li>Privacy Policy</li><li>About Us</li><li>Support</li></ul></div>
    <div class="col address"><h4>Address</h4><ul>
      <li><svg width="16" height="20" viewBox="0 0 16 20"><path d="M8 1a6 6 0 0 0-6 6c0 5 6 12 6 12s6-7 6-12a6 6 0 0 0-6-6z" fill="none" stroke="#fff" stroke-width="1.6"/><circle cx="8" cy="7" r="2" fill="#fff"/></svg>Sed ut perspiciatis unde omnis iste natus error sit</li>
      <li><svg width="16" height="16" viewBox="0 0 16 16"><path d="M3 1h3l1.5 4-2 1.5a9 9 0 0 0 4 4l1.5-2 4 1.5v3a1 1 0 0 1-1 1C7 14 2 9 2 2a1 1 0 0 1 1-1z" fill="#fff"/></svg>+1 555 010 2040</li>
      <li><svg width="18" height="14" viewBox="0 0 18 14"><rect x="1" y="1" width="16" height="12" rx="1.5" fill="none" stroke="#fff" stroke-width="1.5"/><path d="M1 2l8 6 8-6" fill="none" stroke="#fff" stroke-width="1.5"/></svg>info@pellowar.com</li>
    </ul></div>
  </div>
  <div class="copy">© copyrights 2022 Pellowar | All Rights Reserved</div>
</footer>

</body>
</html>
```